"Vine Hollow Excursions" is a top notch Santa Barbara County Wine Tour company.

We provide scenic, boutique and custom wine tours. I need the card to be clean and classy. I will provide our logo. I would like the logo to cover the back side of the card as an option and would like to see a couple color options other then our signature green and gold. I would like to see some creative options and let the designers come up with options.
I need cards for myself and my team. The final design should communicate "An authentic and boutique wine tour experience"
Please use my website for reference www.vinehollowexcursions.example

Target Market(s)

We have a wide range of clients from millennials to baby boomers

Industry/Entity Type

Tour

Contact Information for Business Card

Contact info:
Dale Morton
805-219-6384
info@vinehollowexcursions.example
vinehollowexcursions.example

Colors

Designer to choose colors to be used in the design.

Requirements
Must have
• my logo
Nice to have
• *I would like to have the backside side with the logo and the company statement
• "An authentic and boutique wine tour experience" as an option.
• *I would also like to see what the designers can create!
• *I would like to see an option that incorporates or social: instagram, yelp, trip advisor
Should not have
• I do not want it too busy.

```html
<!DOCTYPE html>
<html lang="en">
<head>
<meta charset="utf-8">
<title>Vine Hollow Excursions – Business Card</title>
<link href="https://fonts.googleapis.com/css2?family=Cinzel:wght@600&family=Open+Sans:wght@400&display=swap" rel="stylesheet">
<style>
  :root {
    --backdrop: #2a2a2a;
    --card-front: #f2f2f1;
    --card-back: #235e3e;
    --brand-green: #1f5a38;
    --ink: #3a3a3a;
    --white: #ffffff;
    --badge-brown: #a48460;
    --badge-green: #5a9a3a;
    --badge-red: #d32323;
  }
  * { margin: 0; padding: 0; box-sizing: border-box; }
  html, body {
    width: 1200px; height: 960px; overflow: hidden;
    background: var(--backdrop);
  }
  .canvas { position: relative; width: 1200px; height: 960px; }
  .card {
    position: absolute; width: 600px; height: 343px;
    box-shadow: 0 3px 8px rgba(0,0,0,.55);
  }
  .card--front { left: 314px; top: 113px; background: var(--card-front); }
  .card--back  { left: 311px; top: 472px; background: var(--card-back); }

  .brand-name {
    position: absolute;
    font-family: "Open Sans", sans-serif; font-weight: 400;
    line-height: 1.25; text-align: center;
  }
  .card--front .brand-name {
    left: 30px; top: 104px; width: 226px;
    font-size: 19px; color: var(--brand-green);
  }
  .card--back .brand-name {
    left: 150px; top: 178px; width: 300px;
    font-size: 24px; color: var(--white);
  }

  .contact {
    position: absolute; right: 34px; top: 220px; text-align: right;
  }
  .contact__name {
    font-family: "Cinzel", serif; font-weight: 600;
    font-size: 24px; color: var(--brand-green);
    letter-spacing: .5px; margin-bottom: 8px;
  }
  .contact__line {
    display: flex; justify-content: flex-end; align-items: center; gap: 8px;
    font-family: "Open Sans", sans-serif; font-size: 14.5px;
    color: var(--ink); line-height: 19px;
  }
  .contact__icon { width: 14px; height: 14px; flex: none; }

  .social {
    position: absolute; right: 30px; top: 31px; display: flex; gap: 4px;
  }
  .social__badge { width: 32px; height: 31px; border-radius: 5px; }
  .social__badge--photo  { background: var(--badge-brown); }
  .social__badge--review { background: var(--badge-green); }
  .social__badge--local  { background: var(--badge-red); }

  .tagline {
    position: absolute; left: 0; right: 0; top: 293px; text-align: center;
    font-family: "Open Sans", sans-serif; font-size: 15px; color: var(--white);
  }
</style>
</head>
<body>
<main class="canvas">
  <section class="card card--front" aria-label="Business card front">
    <div class="brand-name">Vine Hollow<br>Excursions</div>
    <div class="contact">
      <div class="contact__name">DALE MORTON</div>
      <div class="contact__line">
        <span>805-219-6384</span>
        <svg class="contact__icon" viewBox="0 0 14 14" aria-hidden="true">
          <rect x="1" y="3" width="12" height="9" rx="2" fill="var(--brand-green)"/>
          <path d="M2 4 Q7 0 12 4" stroke="var(--brand-green)" stroke-width="2" fill="none"/>
          <circle cx="7" cy="8" r="2" fill="var(--card-front)"/>
        </svg>
      </div>
      <div class="contact__line">
        <span>info@vinehollowexcursions.example</span>
        <svg class="contact__icon" viewBox="0 0 14 14" aria-hidden="true">
          <rect x="1" y="3" width="12" height="8" fill="var(--brand-green)"/>
          <path d="M1 3 L7 8 L13 3" stroke="var(--card-front)" stroke-width="1" fill="none"/>
        </svg>
      </div>
      <div class="contact__line">
        <span>vinehollowexcursions.example</span>
        <svg class="contact__icon" viewBox="0 0 14 14" aria-hidden="true">
          <circle cx="7" cy="7" r="6" fill="var(--brand-green)"/>
          <path d="M1 7 H13 M7 1 V13" stroke="var(--card-front)" stroke-width="1" fill="none"/>
        </svg>
      </div>
    </div>
  </section>

  <section class="card card--back" aria-label="Business card back">
    <div class="social" aria-label="Social profiles">
      <span class="social__badge social__badge--photo"></span>
      <span class="social__badge social__badge--review"></span>
      <span class="social__badge social__badge--local"></span>
    </div>
    <div class="brand-name">Vine Hollow<br>Excursions</div>
    <p class="tagline">An authentic &amp; boutique wine tour experience</p>
  </section>
</main>
</body>
</html>
```